V.Lumo Gin - Bottle label Design

We are manufacturers of Gin in South Africa.
The name of our Gin is V.Lumo Gin with Q standing for Dlovikazi, a Xhosa Village in the region of Eastern Cape.

We would like our brand to depict the following (really the focus of Gold on it)
> Prosperity of the place
> Wealth of the place, land, material or in the people
> Gold rush, potential, hope

As the brand matures, we would like to have campaigns with it. See ideas below:
> V.Lumo Premium
> Crimson dusk edition
Limited edition will be released every year
- V.Lumo entabeni (location)
- V.Lumo ekhayeni (location)

> Each batch of bottles with focus on a specific area/location in Dlovikazi. One that is known and will be highlighted on the map design of the bottle.
Bottles based on landmarks in Dlovikazi and landmark design in the Big V.

Below we tried but we are not where we really want to be in terms of Gin Bottle elegance.

Target Market(s)

Target market is the young crowd. Young Xhosa men and women working really hard to get their goals. Positive thinkers. Elegant. Fresh. Bold. Age from 24 to 45. People who enjoy quality products.

Industry/Entity Type

Beverage Industry. Craft Gin.

Font styles to use
Sans Serif
Decorative

Colors
FFF300
FFF600
FEFA6F
FFFEC7
FFFEE8
FFC000
F8CF3A
FAE287
FDF2CF
FEFAEE

Requirements
Must have
• Gold colour as a theme. Try and make the background textured.

```html
<!DOCTYPE html>
<html lang="en">
<head>
<meta charset="utf-8">
<title>V.Lumo Gin – Bottle Label</title>
<link rel="stylesheet" href="https://fonts.googleapis.com/css2?family=Josefin+Sans:wght@300&family=Barlow+Semi+Condensed:wght@500&family=Barlow+Condensed:wght@400&display=swap">
<style>
  :root {
    --page: #ffffff;
    --label-edge: #e4e4e4;
    --panel: #e7e7e9;
    --stripe: #d3cabb;
    --ink: #1b1b1b;
    --gold-dark: #6b4408;
    --gold-olive: #9c8a2a;
    --gold-bright: #e9e96a;
    --gold-mid: #c9a43a;
    --gold-amber: #a8701c;
    --band-text: #fdf2a8;
    --gold-gradient: linear-gradient(90deg, var(--gold-dark) 0%, var(--gold-olive) 18%, var(--gold-bright) 34%, var(--gold-mid) 55%, var(--gold-amber) 72%, var(--gold-dark) 100%);
  }
  * { margin: 0; padding: 0; box-sizing: border-box; }
  html, body { width: 1200px; height: 1200px; overflow: hidden; background: var(--page); }
  .canvas { position: relative; width: 1200px; height: 1200px; }

  .label {
    position: absolute; left: 184px; top: 267px; width: 840px; height: 672px;
    background: var(--label-edge);
  }
  .label-frame {
    position: absolute; left: 4px; top: 4px; right: 4px; bottom: 3px;
    background: var(--gold-gradient);
  }
  .label-panel {
    position: absolute; left: 20px; top: 21px; width: 799px; height: 631px;
    background: var(--panel);
  }
  .texture {
    position: absolute; left: 10px; top: 6px; width: 780px; height: 487px;
    background: repeating-linear-gradient(180deg, transparent 0 7px, var(--stripe) 7px 9.5px);
    opacity: 0.85;
  }
  .landscape {
    position: absolute; left: 21px; top: 18px; width: 756px; height: 288px;
    background: linear-gradient(90deg, rgba(156,138,42,.45) 0%, rgba(233,233,106,.45) 35%, rgba(201,164,58,.45) 62%, rgba(168,112,28,.45) 100%);
  }
  .brand-mark {
    position: absolute; left: 130px; top: 215px; width: 166px; height: 166px;
    border-radius: 50%; background: var(--gold-mid);
  }
  .brand-name {
    position: absolute; left: 315px; top: 279px;
    font-family: "Josefin Sans", sans-serif; font-weight: 300;
    font-size: 110px; line-height: 1; letter-spacing: 0; color: var(--ink);
    white-space: nowrap;
  }
  .product-type {
    position: absolute; left: 327px; top: 398px;
    font-family: "Josefin Sans", sans-serif; font-weight: 300;
    font-size: 90px; line-height: 1; letter-spacing: 0; color: var(--ink);
  }
  .info-table {
    position: absolute; left: 10px; top: 506px; width: 780px; height: 52px;
    display: grid; grid-template-columns: 483px 127px 1fr;
    border-top: 3px solid var(--ink); border-bottom: 3px solid var(--ink);
    font-family: "Barlow Semi Condensed", sans-serif; font-weight: 500;
    font-size: 23px; letter-spacing: 1px; color: var(--ink);
  }
  .info-cell { display: flex; align-items: center; justify-content: center; white-space: nowrap; }
  .info-cell + .info-cell { border-left: 3px solid var(--ink); }
  .info-origin { justify-content: flex-start; padding-left: 44px; }
  .tagline-band {
    position: absolute; left: 10px; top: 568px; width: 780px; height: 52px;
    background: var(--gold-gradient);
    display: flex; align-items: center; justify-content: center;
    font-family: "Barlow Condensed", sans-serif; font-weight: 400;
    font-size: 21px; letter-spacing: 0.8px; color: var(--band-text);
    white-space: nowrap;
  }
</style>
</head>
<body>
<div class="canvas">
  <section class="label">
    <div class="label-frame"></div>
    <div class="label-panel">
      <div class="texture"></div>
      <div class="landscape" role="img" aria-label="Gold-foil illustration of the hills and homesteads of Dlovikazi village"></div>
      <div class="brand-mark"></div>
      <h1 class="brand-name">V.LUMO</h1>
      <p class="product-type">GIN</p>
      <div class="info-table">
        <div class="info-cell info-origin">Made in Dlovikazi vs The Eastern Cape</div>
        <div class="info-cell">750 ml</div>
        <div class="info-cell">43% alc.vol.</div>
      </div>
      <div class="tagline-band">TRIPLE DISTILLED WITH JUNIPER BERRIES, CITRUS PEALS AND THE AROMAS OF DLOVIKAZI</div>
    </div>
  </section>
</div>
</body>
</html>
```